design a construction company business card

Design business card around our logo. Card must have all the typical info: name, title, address, phone, email, business name, etc. Somewhere on the card I would like to see our motto "Founded on Trust... Driven by Dedication." Consider adding a splash of bright orange to the card to complement the blues and silvers/grays in the logo. We are open to metallic inks, textures, etc. We would like to see options on both light and dark backgrounds. The font in the logo is Euro Technic Extended Regular.

```html
<!DOCTYPE html>
<html lang="en">
<head>
<meta charset="utf-8">
<title>Halloran Builders – Business Card</title>
<link rel="stylesheet" href="https://fonts.googleapis.com/css2?family=Maven+Pro:wght@400;500;700&display=swap">
<style>
  :root {
    --stage: #1a1b1d;
    --card: #1c1d20;
    --card-edge: #232428;
    --brand-blue: #2a6fc0;
    --band-blue: #2f74c4;
    --text-light: #e9ebee;
    --motto-dark: #0b0b0c;
    --motto-light: #dfe1e4;
  }
  * { margin: 0; padding: 0; box-sizing: border-box; }
  html, body { width: 1200px; height: 1000px; overflow: hidden; }
  body {
    background: var(--stage);
    font-family: "Maven Pro", sans-serif;
    position: relative;
  }
  .card {
    position: absolute;
    left: 256px;
    width: 687px;
    height: 393px;
    background: radial-gradient(ellipse at 60% 30%, var(--card-edge), var(--card) 70%);
  }
  .card::after {
    content: "";
    position: absolute;
    left: 0; right: 0; bottom: 0;
    height: 10px;
    background: var(--band-blue);
  }
  .card--front { top: 72px; }
  .card--back { top: 538px; }

  .front-name {
    position: absolute;
    left: 0; right: 0;
    top: 170px;
    text-align: center;
    font-size: 40px;
    line-height: 48px;
    font-weight: 500;
    letter-spacing: 5px;
    color: var(--brand-blue);
  }
  .motto {
    position: absolute;
    left: 0; right: 0;
    top: 293px;
    text-align: center;
    font-size: 16px;
    line-height: 20px;
    font-weight: 700;
    letter-spacing: 0.6px;
    white-space: nowrap;
  }
  .motto span {
    background: linear-gradient(90deg, var(--motto-dark) 0%, var(--motto-dark) 60%, var(--motto-light) 85%);
    -webkit-background-clip: text;
    background-clip: text;
    color: transparent;
  }

  .brand {
    position: absolute;
    left: 89px;
    top: 186px;
    display: flex;
    align-items: center;
    gap: 10px;
    white-space: nowrap;
    color: var(--brand-blue);
    font-size: 18px;
    line-height: 22px;
    font-weight: 500;
    letter-spacing: 0.5px;
  }
  .brand-mark { width: 14px; height: 14px; background: var(--brand-blue); flex: none; }

  .divider {
    position: absolute;
    left: 349px;
    top: 84px;
    width: 2px;
    height: 221px;
    background: var(--brand-blue);
  }
  .details {
    position: absolute;
    left: 380px;
    top: 80px;
    color: var(--text-light);
  }
  .person-name {
    font-size: 24px;
    font-weight: 400;
    color: var(--brand-blue);
    letter-spacing: 0.5px;
    line-height: 28px;
  }
  .person-name strong { font-weight: 700; }
  .person-title { font-size: 16.5px; line-height: 20px; }
  .person-title span { color: var(--brand-blue); }
  .address { margin-top: 10px; font-size: 17px; line-height: 22px; }
  .contacts { list-style: none; margin-top: 12px; }
  .contacts li {
    display: flex;
    align-items: center;
    gap: 8px;
    font-size: 17px;
    height: 28px;
    margin-left: -2px;
  }
  .contacts svg { width: 20px; height: 20px; fill: var(--brand-blue); flex: none; }
</style>
</head>
<body>

<section class="card card--front">
  <div class="front-name">HALLORAN</div>
  <p class="motto"><span>Founded on Trust... Driven by Dedication</span></p>
</section>

<section class="card card--back">
  <div class="brand"><span class="brand-mark"></span>Halloran Builders, Inc.</div>
  <div class="divider"></div>
  <div class="details">
    <h1 class="person-name"><strong>MARCUS</strong> DELANEY</h1>
    <p class="person-title">CEO of <span>Halloran Builders, INC</span></p>
    <p class="address">118/4 Ridge Rd, Eastwood<br>NSW 2122, NY</p>
    <ul class="contacts">
      <li>
        <svg viewBox="0 0 24 24"><path d="M6.6 10.8a15.1 15.1 0 0 0 6.6 6.6l2.2-2.2c.3-.3.7-.4 1-.2 1.1.4 2.3.6 3.6.6.6 0 1 .4 1 1V20c0 .6-.4 1-1 1A17 17 0 0 1 3 4c0-.6.4-1 1-1h3.5c.6 0 1 .4 1 1 0 1.3.2 2.5.6 3.6.1.3 0 .7-.2 1z"/></svg>
        (02) 5550 1842
      </li>
      <li>
        <svg viewBox="0 0 24 24"><path d="M7 2h10a2 2 0 0 1 2 2v16a2 2 0 0 1-2 2H7a2 2 0 0 1-2-2V4a2 2 0 0 1 2-2zm0 3v13h10V5zm5 14.2a1 1 0 1 0 0 .1z"/></svg>
        0491 570 233
      </li>
      <li>
        <svg viewBox="0 0 24 24"><path d="M3 5h18v14H3zm2 2v.5l7 4.5 7-4.5V7zm0 2.8V17h14V9.8l-7 4.5z"/></svg>
        info@halloranbuilders.com
      </li>
      <li>
        <svg viewBox="0 0 24 24"><path d="M12 2a10 10 0 1 0 0 20 10 10 0 0 0 0-20zm-1 17.9A8 8 0 0 1 4.2 10.3L9 15v1a2 2 0 0 0 2 2zm6.9-2.5A2 2 0 0 0 16 16h-1v-3a1 1 0 0 0-1-1H8v-2h2a1 1 0 0 0 1-1V7h2a2 2 0 0 0 2-2v-.4a8 8 0 0 1 2.9 12.8z"/></svg>
        www.halloranbuilders.com
      </li>
    </ul>
  </div>
</section>

</body>
</html>
```